Brightline Energy Product Distribution Brochure

We are looking to have our current brochure for our customers completely redesigned...the idea is to present the relevant information in an attractive way . Our website is brightlineenergyco.example where you can find more information about us. We have included a file with a rough idea of the page order and what each should include but feel free to adapt based on design. The example provided is only for context and doesnt have to be maintained. We will be using the brochure both digitally and in print form. As long as it reads easily and is eye catching, the design can be horizontal or vertical.Final deliverable should be indesign file.

"Our Brands" page: should be limited to one page (space being enough) where it has the header for each one (for example diesel generators) space for one or two lines of text and then the corresponding logos for each of the five categories
Updates

For those asking: the "our brands" page should be a single page layout where there is a header with the corresponding section and space for maybe one line of text followed by the two logos for that category. Each of the product pages should be similar in fashion to the one in the document attached: a photo of the product with some white space and space for the text to be included. We will be posting additional examples today

Target Market(s)

We want to present it to customers both digitally and in print so they can see our products

Industry/Entity Type

Power Generation

Font styles to use
Serif

Requirements
Must have
• Eye catching and able to present the information in a presentable fashion. Rest is up to you.
Nice to have
• Should incorporate the colors of our logo but can also add other depending on design

```html
<!DOCTYPE html>
<html lang="en">
<head>
<meta charset="utf-8">
<title>Brightline Energy – Distributor Program Guide</title>
<link href="https://fonts.googleapis.com/css2?family=Montserrat:ital,wght@0,300;0,400;0,500;0,700;1,300&display=swap" rel="stylesheet">
<style>
  :root{
    --yellow:#fccb05;
    --yellow-deep:#e8b800;
    --charcoal:#3d3b3a;
    --ink:#1d1d1b;
    --label:#6b6b6b;
    --paper:#ffffff;
    --board:#ffffff;
  }
  *{box-sizing:border-box;margin:0;padding:0}
  html,body{width:1200px;height:1200px;overflow:hidden;background:var(--board)}
  body{position:relative;font-family:"Montserrat",Arial,sans-serif;color:var(--ink)}

  .view-label{position:absolute;top:136px;font-size:24px;font-weight:300;font-style:italic;color:var(--label)}
  .view-label--cover{left:31px}
  .view-label--inside{left:613px}

  .page{position:absolute;background:var(--paper);overflow:hidden;box-shadow:0 20px 40px rgba(0,0,0,.18)}
  .page--cover{left:32px;top:216px;width:542px;height:766px}
  .page--inside{left:616px;top:216px;width:544px;height:768px}
  .page__shapes{position:absolute;inset:0;width:100%;height:100%}

  .product-photo{position:absolute;border-radius:3px;background:linear-gradient(90deg,#2a2a2a 0%,#9c8a6a 45%,#d9d9d9 65%,#1f1f1f 100%)}
  .page--cover .product-photo{left:206px;top:470px;width:322px;height:124px}
  .page--inside .product-photo{left:282px;top:554px;width:246px;height:96px}

  .brandmark{position:absolute;display:flex;align-items:center;gap:6px;font-weight:400;color:var(--ink);white-space:nowrap}
  .brandmark__square{display:block;background:var(--yellow)}
  .page--cover .brandmark{left:312px;top:402px;font-size:14px}
  .page--cover .brandmark__square{width:12px;height:12px}
  .page--inside .brandmark{left:380px;top:38px;font-size:9px}
  .page--inside .brandmark__square{width:9px;height:9px}

  .cover-title{position:absolute;left:66px;top:92px;font-weight:400;font-size:36px;line-height:36px;text-transform:uppercase;letter-spacing:-.3px}
  .cover-title__line{display:block}
  .cover-title__line--light{color:#fff}
  .cover-title__line--accent{color:var(--yellow)}
  .cover-rule{position:absolute;left:66px;top:181px;width:186px;height:1px;background:var(--yellow)}
  .cover-subtitle{position:absolute;left:66px;top:193px;font-weight:300;font-size:17px;line-height:18px;color:#fff;text-transform:uppercase;letter-spacing:-.3px}

  .section-tab{position:absolute;left:0;top:34px;width:46px;height:10px;background:var(--yellow)}
  .section-label{position:absolute;left:55px;top:34px;font-size:11px;line-height:11px;text-transform:uppercase}
  .toc-title{position:absolute;left:46px;top:106px;font-weight:300;font-size:32px;text-transform:uppercase;letter-spacing:-.5px}
  .toc{position:absolute;left:46px;top:164px;width:330px;list-style:none}
  .toc__item{position:relative;padding-left:26px;height:29.6px}
  .toc__item::before{content:"";position:absolute;left:4px;top:3px;width:6px;height:6px;background:var(--yellow);transform:rotate(45deg)}
  .toc__head{display:flex;font-weight:700;font-size:8.6px;line-height:10px}
  .toc__head span:first-child{white-space:nowrap}
  .toc__dots{flex:1;border-bottom:1px dotted var(--ink);margin:0 1px 2px}
  .toc__desc{font-size:8.6px;line-height:11px}

  .page-footer{position:absolute;top:738px;font-size:7.5px;font-weight:700}
  .page-footer--num{left:47px}
  .page-footer--url{left:98px;text-transform:uppercase}
</style>
</head>
<body>
  <p class="view-label view-label--cover">Front Cover</p>
  <p class="view-label view-label--inside">Inside</p>

  <section class="page page--cover">
    <svg class="page__shapes" viewBox="0 0 677 958" preserveAspectRatio="none">
      <defs>
        <linearGradient id="coverDark" x1="0" y1="0" x2="1" y2="1">
          <stop offset="0" stop-color="#4a4746"/><stop offset=".5" stop-color="#3a3837"/><stop offset="1" stop-color="#454241"/>
        </linearGradient>
        <linearGradient id="coverCorner" x1="0" y1="0" x2="1" y2="1">
          <stop offset="0" stop-color="#f2f2f2"/><stop offset="1" stop-color="#d6d6d6"/>
        </linearGradient>
      </defs>
      <rect width="677" height="620" fill="url(#coverDark)" role="img" aria-label="Dark industrial backdrop of interlocking machine gears"/>
      <polygon points="440,308 677,545 677,958 0,958 0,660 88,660" fill="var(--yellow)"/>
      <polygon points="0,660 88,660 0,748" fill="var(--yellow-deep)"/>
      <polygon points="482,355 677,550 677,712 467,922 192,645" fill="#fff"/>
      <polygon points="580,958 677,862 677,958" fill="url(#coverCorner)"/>
      <polyline points="0,240 198,440 20,620" fill="none" stroke="var(--yellow)" stroke-width="1.5"/>
      <polyline points="677,45 497,225 677,405" fill="none" stroke="var(--yellow)" stroke-width="1.5"/>
      <polyline points="5,958 162,793 325,958" fill="none" stroke="#fff" stroke-opacity=".7" stroke-width="1.5"/>
    </svg>
    <h1 class="cover-title">
      <span class="cover-title__line cover-title__line--light">Distributor</span>
      <span class="cover-title__line cover-title__line--accent">Program Guide</span>
    </h1>
    <div class="cover-rule"></div>
    <p class="cover-subtitle">Diesel Generators,<br>Alternators &amp; Parts</p>
    <div class="brandmark"><span class="brandmark__square"></span>Brightline Energy</div>
    <div class="product-photo" role="img" aria-label="Lineup of industrial diesel generator sets and an engine"></div>
  </section>

  <section class="page page--inside">
    <svg class="page__shapes" viewBox="0 0 680 960" preserveAspectRatio="none">
      <defs>
        <linearGradient id="insideShade" x1="0" y1="0" x2="1" y2="0">
          <stop offset="0" stop-color="#ffffff"/><stop offset="1" stop-color="#e4e4e4"/>
        </linearGradient>
      </defs>
      <polygon points="505,498 680,673 680,960 0,960 0,763 240,763" fill="var(--yellow)"/>
      <polygon points="540,533 680,673 680,807 525,960 318,755" fill="#fff"/>
      <polygon points="600,593 680,673 680,560" fill="url(#insideShade)"/>
      <polyline points="679,210 498,392 679,572" fill="none" stroke="var(--yellow)" stroke-width="1.5"/>
      <polyline points="0,530 137,670 45,762" fill="none" stroke="var(--yellow)" stroke-width="1.5"/>
    </svg>
    <div class="section-tab"></div>
    <p class="section-label">Index</p>
    <div class="brandmark"><span class="brandmark__square"></span>Brightline Energy</div>
    <h2 class="toc-title">Table of Content</h2>
    <ol class="toc">
      <li class="toc__item"><div class="toc__head"><span>Epero in ere nimporemquam es quisimus</span><span class="toc__dots"></span><span>01</span></div><p class="toc__desc">Eperporemquo in ere nimporemquam es quisporemquimus</p></li>
      <li class="toc__item"><div class="toc__head"><span>Magnis eria vitaquo dionsed ex estrum fugitia dolorpor</span><span class="toc__dots"></span><span>02</span></div><p class="toc__desc">Sim dentiam ernam abor aut volum ipid qui cus, officium</p></li>
      <li class="toc__item"><div class="toc__head"><span>Axim erest, quas serios dolesti onsecae dolore quun</span><span class="toc__dots"></span><span>03</span></div><p class="toc__desc">Unt, nem restrum a volenistotat quam, im alitae et et aut</p></li>
      <li class="toc__item"><div class="toc__head"><span>Nam, volorrumque volorate plique labo</span><span class="toc__dots"></span><span>04</span></div><p class="toc__desc">Am, iust volutem il moluptati derumet et volorro rrovid qui</p></li>
      <li class="toc__item"><div class="toc__head"><span>Nam endit qui aut dolorrum quistrumqui in</span><span class="toc__dots"></span><span>05</span></div><p class="toc__desc">Debitetur Magnati orendam expelec atempe vendent</p></li>
      <li class="toc__item"><div class="toc__head"><span>Axim erest, quas serios dolesti onsecae</span><span class="toc__dots"></span><span>06</span></div><p class="toc__desc">Unt, nem restrum a volenistotat quam, im alitae et et aut</p></li>
      <li class="toc__item"><div class="toc__head"><span>Nam, volorrumque volorate plique labo am, iust volutem</span><span class="toc__dots"></span><span>07</span></div><p class="toc__desc">Derumet et volorro rrovid qui doluptiae</p></li>
      <li class="toc__item"><div class="toc__head"><span>Endit qui aut dolorrum quistrumqui in ped</span><span class="toc__dots"></span><span>08</span></div><p class="toc__desc">Debitetur Magnati orendam expelec atempe vendent</p></li>
      <li class="toc__item"><div class="toc__head"><span>Axim erest, quas serios dolesti onsecae vidunt abo</span><span class="toc__dots"></span><span>09</span></div><p class="toc__desc">Unt, nem restrum a volenistotat quam, im alitae</p></li>
    </ol>
    <div class="product-photo" role="img" aria-label="Lineup of industrial diesel generator sets and an engine"></div>
    <p class="page-footer page-footer--num">2</p>
    <p class="page-footer page-footer--url">www.brightlineenergyco.example</p>
  </section>
</body>
</html>
```